Informational Site for Advanced Chemistry R&D

The company develops oxidation chemistry for air, water, fuel pollution controls. The site has been prototyped at www.velquaresearch.example. Take a look. Now, the task is to design it for eye-catching beauty with use of color, on-page scroll-driven color transition and parallax effects. Should capture the themes: high technology, wow it's beautiful, modern, uncluttered, clean urban environment.

Target Market(s)

China Environmentally Conscious Government and Industry,

Industry/Entity Type

It Company

Number of Pages Required

3 page

Font styles to use
Sans Serif

Requirements
Must have
• Parallax effects, desktop compatible, Rich, Modern, Simple, Graphic
Nice to have
• Mobile Phone Compatible
Should not have
• Flash, or anything that is slow to load or requires high bandwidth

```html
<!DOCTYPE html>
<html lang="en">
<head>
<meta charset="utf-8">
<title>Velqua Research — Advanced Oxidation Science</title>
<link href="https://fonts.googleapis.com/css2?family=Open+Sans:wght@400;600;700&display=swap" rel="stylesheet">
<style>
:root{
  --teal:#2bb5b0;
  --blue:#1f6fb5;
  --blue-head:#1b7db6;
  --map-blue:#2a7dc4;
  --text:#555;
  --rule:#d6d6d6;
  --pale:#f3f3f3;
  --footer:#3b3b3b;
  --white:#fff;
}
*{margin:0;padding:0;box-sizing:border-box}
html,body{width:1200px;height:3358px;overflow:hidden}
body{font-family:"Open Sans",Arial,sans-serif;color:var(--text);position:relative;background:var(--white)}
.abs{position:absolute}
.btn{position:absolute;display:block;background:var(--blue);color:var(--white);font-size:15px;font-weight:600;text-align:center;line-height:48px;height:48px;text-decoration:none;text-transform:uppercase}

/* hero */
.hero{top:0;left:0;width:1200px;height:617px;background:linear-gradient(180deg,#2c5aa0 0%,#5f86bf 32%,#8a8f8d 62%,#4f5b55 80%,#6c8aa3 100%)}
.hero-top{top:0;left:0;width:1200px;height:6px;background:var(--teal)}
.logo{display:flex;align-items:center;gap:10px;color:var(--teal);font-weight:700;font-size:26px}
.logo .dot{width:22px;height:22px;border-radius:50%;background:var(--teal)}
.hero .logo{top:84px;left:75px}
.nav{top:60px;left:680px;display:flex;align-items:center;gap:44px;font-size:14px;color:var(--white);font-weight:600}
.nav .home{width:60px;height:60px;border-radius:50%;border:3px solid var(--teal);color:var(--teal);display:flex;align-items:center;justify-content:center;font-size:13px}
.hero h1{top:262px;left:0;width:1200px;text-align:center;color:var(--white);font-size:44px;line-height:53px;font-weight:700;text-shadow:0 2px 6px rgba(0,0,0,.35)}
.arrow{top:262px}

/* section heads */
.divider{left:75px;width:1050px;height:1px;background:var(--rule)}
.divider::after{content:"";position:absolute;left:508px;top:-17px;width:34px;height:34px;border-radius:50%;background:var(--white);border:3px solid var(--blue-head)}
.sec-title{left:0;width:1200px;text-align:center;color:var(--blue-head);font-size:31px;font-weight:600}

.welcome p{top:776px;left:80px;width:1040px;text-align:center;font-size:14px;line-height:24px}

/* advanced oxidation */
.oxidation{top:995px;left:0;width:1200px;height:417px;background:var(--pale)}
.oxidation .panel{top:0;left:0}
.oxidation .copy{top:50px;left:75px;width:570px;color:var(--white);font-size:14px;line-height:24px}
.oxidation h2{font-size:32px;font-weight:400;margin-bottom:20px}
.oxidation ul{list-style:none;margin:6px 0}
.oxidation li{display:flex;align-items:center;gap:10px;margin:2px 0}
.tick{width:16px;height:16px;border-radius:50%;background:var(--white);display:inline-flex;align-items:center;justify-content:center}
.diagram{top:20px;left:780px;width:345px;height:377px;border-radius:8px;background:radial-gradient(circle at 50% 45%,#f7d12a 0 9%,#ffffff 28%,#f3f3f3 70%)}

/* solutions */
.card{top:1570px;width:330px}
.card .photo{height:127px}
.card h3{margin-top:86px;color:var(--teal);font-size:17px;font-weight:600}
.card p{margin-top:6px;font-size:14px;line-height:23px;height:72px}

.cityband{top:1995px;left:0;width:1200px;height:278px;background:linear-gradient(180deg,#3a5a8c 0%,#6f86a5 45%,#5d6a6d 75%,#2f4660 100%)}

/* partners */
.partner{top:2455px;width:260px;text-align:center;font-size:14px;color:#444}
.partner .badge{width:96px;height:96px;margin:0 auto 18px;border-radius:50%}

/* contact */
.contact{top:2643px;left:0;width:1200px;height:277px;background:var(--teal)}
.contact .divider{background:rgba(255,255,255,.45)}
.contact .divider::after{background:var(--teal);border-color:var(--white)}
.contact .sec-title{color:var(--white)}
.contact p{top:153px;left:0;width:1200px;text-align:center;color:var(--white);font-size:14px;line-height:28px}

.map-row{top:2920px;left:0;width:1200px;height:313px}
.address{top:90px;left:780px;color:var(--white);font-size:14px;line-height:28px}
.address h4{font-size:19px;font-weight:700;margin-bottom:2px}
.address .line{display:flex;align-items:center;gap:12px}

.footer{top:3233px;left:0;width:1200px;height:125px;background:var(--footer)}
.footer .logo{top:46px;left:75px;color:#9a9a9a;font-size:22px}
.footer .logo .dot{background:#9a9a9a}
.footer .legal{top:40px;left:225px;color:#8c8c8c;font-size:13px;line-height:22px}
.social{top:40px;left:895px;display:flex;gap:10px}
.social span{width:38px;height:38px;border-radius:50%;border:2px solid #8c8c8c}
</style>
</head>
<body>

<header class="abs hero" role="img" aria-label="City skyline reflected in a river under a blue sky">
  <div class="abs hero-top"></div>
  <div class="abs logo"><span class="dot"></span>Velqua</div>
  <nav class="abs nav">
    <span class="home">HOME</span><span>TECHNOLOGY</span><span>PRODUCTS</span><span>CONTACT</span>
  </nav>
  <svg class="abs arrow" style="left:75px" width="28" height="100" viewBox="0 0 28 100"><polyline points="26,2 2,50 26,98" fill="none" stroke="#fff" stroke-width="2"/></svg>
  <svg class="abs arrow" style="left:1097px" width="28" height="100" viewBox="0 0 28 100"><polyline points="2,2 26,50 2,98" fill="none" stroke="#fff" stroke-width="2"/></svg>
  <h1 class="abs">ADVANCED OXIDATION<br>SCIENCE FOR ENVIRONMENTAL<br>POLLUTION MANAGEMENT</h1>
</header>

<section class="welcome">
  <div class="abs divider" style="top:683px"></div>
  <h2 class="abs sec-title" style="top:716px">WELCOME TO OUR WEBSITE</h2>
  <p class="abs">Velqua Research develops advanced oxidation technologies and materials, which it licenses to Velqua Systems, China. Velqua Systems is engaged in the sales, service and support of environmental solutions for industry and government. With offices in Shanghai, Beijing, Shijiazhuang, and Chengdu, Velqua Systems is among the most advanced and rapidly growing companies offering solutions for air, water and fuel environmental compliance.</p>
  <a class="btn" href="#" style="top:883px;left:517px;width:166px">Learn More</a>
</section>

<section class="abs oxidation">
  <svg class="abs panel" width="1200" height="417" viewBox="0 0 1200 417"><polygon points="0,0 643,0 746,417 0,417" fill="#2bb5b0"/></svg>
  <div class="abs diagram" role="img" aria-label="Diagram of hydroxyl radical reactions with pollutant molecules"></div>
  <div class="abs copy">
    <h2>Advanced Oxidation</h2>
    <p>Advanced Oxidation refers to a variety of techniques employing the Hydroxyl Radical, an energetic, highly reactive cousin of the water molecule.</p>
    <ul>
      <li><span class="tick"><svg width="10" height="10" viewBox="0 0 10 10"><polyline points="1,5 4,8 9,2" fill="none" stroke="#2bb5b0" stroke-width="2"/></svg></span>To add oxygen to inorganic molecules</li>
      <li><span class="tick"><svg width="10" height="10" viewBox="0 0 10 10"><polyline points="1,5 4,8 9,2" fill="none" stroke="#2bb5b0" stroke-width="2"/></svg></span>To remove hydrogen from organic molecules</li>
    </ul>
    <p>These transformations convert important industrial contaminants into reactive forms that can be captured or that disintegrate into harmless end products.</p>
  </div>
  <a class="btn" href="#" style="top:307px;left:75px;width:165px">Learn More</a>
</section>

<section class="solutions">
  <div class="abs divider" style="top:1460px"></div>
  <h2 class="abs sec-title" style="top:1494px">OUR SOLUTIONS</h2>

  <article class="abs card" style="left:75px">
    <div class="photo" role="img" aria-label="Refinery pipework and towers" style="background:linear-gradient(180deg,#c9ccd0,#4a4f55)"></div>
    <h3>Fuel Oil Desulfurization</h3>
    <p>Our proprietary low temperature and pressure advanced oxidation catalytic process reliably removes sulfur ..</p>
    <a class="btn" href="#" style="left:0;top:335px;width:165px">Learn More</a>
  </article>
  <article class="abs card" style="left:435px">
    <div class="photo" role="img" aria-label="Worker handling chemical containers" style="background:linear-gradient(135deg,#8aa0b5,#2e4a78 55%,#c9c2b3)"></div>
    <h3>Volatile Organic Compunds (VOC)</h3>
    <p>Alkanes, alkenes, halogenated hydrocarbons, aromatic hydrocarbons, esters, aldehydes, polycyclic aromatic hydrocarbons.</p>
    <a class="btn" href="#" style="left:0;top:335px;width:165px">Learn More</a>
  </article>
  <article class="abs card" style="left:795px">
    <div class="photo" role="img" aria-label="Smoke stacks emitting flue gas" style="background:linear-gradient(180deg,#dcdde0,#7b7f87 60%,#3e4047)"></div>
    <h3>Flue Gas Scrubbing</h3>
    <p>Desulfurization and denitrification using our proprietary flue gas advanced oxidation catalytic process (FGAOC).</p>
    <a class="btn" href="#" style="left:0;top:335px;width:165px">Learn More</a>
  </article>
</section>

<div class="abs cityband" role="img" aria-label="City skyline by the river under a darkened blue sky"></div>

<section class="partners">
  <div class="abs divider" style="top:2330px"></div>
  <h2 class="abs sec-title" style="top:2364px">OUR PARTNERS</h2>
  <div class="abs partner" style="left:45px"><div class="badge" style="background:#2bb5b0"></div>Our sales partner in China</div>
  <div class="abs partner" style="left:340px"><div class="badge" style="background:#d8462a"></div>Our construction partner in China</div>
  <div class="abs partner" style="left:635px"><div class="badge" style="background:#2a5d9a"></div>Our technology partner in China</div>
  <div class="abs partner" style="left:930px"><div class="badge" style="background:#b3202e"></div>Our technology partner in China</div>
</section>

<section class="abs contact">
  <div class="abs divider" style="top:64px"></div>
  <h2 class="abs sec-title" style="top:96px">CONTACT US</h2>
  <p class="abs">We welcome inquiries regarding the licensing, distribution, and purchase of our products, systems, and technologies.<br>Please contact us for more information.</p>
</section>

<section class="abs map-row">
  <svg class="abs" width="1200" height="313" viewBox="0 0 1200 313">
    <rect width="1200" height="313" fill="#2a7dc4"/>
    <polygon points="0,0 655,0 735,313 0,313" fill="#e8e4d8" role="img" aria-label="Street map of the office area"/>
  </svg>
  <div class="abs address">
    <h4>VELQUA RESEARCH CORPORATION</h4>
    <div>Harbor Point, U.S.A.</div>
    <div class="line"><svg width="14" height="10" viewBox="0 0 14 10"><rect x="0.5" y="0.5" width="13" height="9" fill="none" stroke="#fff"/><polyline points="1,1 7,6 13,1" fill="none" stroke="#fff"/></svg>info@velquaresearch.example</div>
    <div class="line"><svg width="14" height="14" viewBox="0 0 14 14"><path d="M3 1l3 3-2 2c1 2 2 3 4 4l2-2 3 3-2 2C6 13 1 8 1 3z" fill="#fff"/></svg>+1 555 014 2288</div>
  </div>
</section>

<footer class="abs footer">
  <div class="abs logo"><span class="dot"></span>Velqua</div>
  <div class="abs legal">Copyright © 2016.<br>All Right Reserved | Privacy Policy</div>
  <div class="abs social"><span></span><span></span><span></span><span></span><span></span></div>
</footer>

</body>
</html>
```